CBD AgriBusiness Verdant Trophy Business Card

We are HiTec producer of medical cannabis CBD Switzerland of high quality. Our website is alpinleaf.net, we will also revisit it graphically, the winner of this contest will be the graphic designer chosen for the new design of the website. We stand out by the skill of the team, many of our engineers we win cup cannabis. I join the current map to take as an example but to revisit completely: deletion of surname and first name, modification of funds (front / back), reorganization of text info, highlighting the address of the website. three characteristics define the business card: Professional, Class, refined. The business card must be optimized for soft-touch and selective varnish printing.

Target Market(s)

Customers and Suppliers

Industry/Entity Type

Agribusiness

Contact Information for Business Card

Logo, Tél / Whatsapp, mail, url du site : alpinleaf.net

Font styles to use
Sans Serif

Requirements
Must have
• Logo of alpinleaf.net
Nice to have
• a design that stands out well on the selective varnish
Should not have
• Last name and first name

```html
<!DOCTYPE html>
<html lang="en">
<head>
<meta charset="utf-8">
<title>alpinleaf business card</title>
<link rel="stylesheet" href="https://fonts.googleapis.com/css2?family=Work+Sans:wght@400;700;800&display=swap">
<style>
  :root {
    --backdrop: #a9a9a9;
    --card: #0c0d0c;
    --card-edge: #1d201d;
    --green: #8dd15a;
    --leaf-dark: rgba(30, 42, 18, 0.9);
    --leaf-mid: #4f6a2a;
    --leaf-light: #7f9a47;
    --white: #ffffff;
    --muted: #e6e6e6;
  }
  * { margin: 0; padding: 0; box-sizing: border-box; }
  html, body { width: 1200px; height: 930px; overflow: hidden; }
  body {
    background: radial-gradient(ellipse at 50% 45%, #c4c4c4 0%, var(--backdrop) 75%);
    font-family: "Work Sans", Arial, sans-serif;
    position: relative;
  }
  .card {
    position: absolute;
    width: 560px;
    height: 320px;
    border-radius: 22px;
    background: linear-gradient(135deg, var(--card-edge) 0%, var(--card) 55%, #050605 100%);
    overflow: hidden;
    box-shadow: 0 14px 30px rgba(0,0,0,0.35);
  }
  .card--front { left: 80px; top: 110px; }
  .card--back { left: 560px; top: 500px; }
  .leaf-photo {
    position: absolute;
    inset: 0;
    background: radial-gradient(circle 190px at 470px 80px, var(--leaf-light) 0%, var(--leaf-mid) 40%, var(--leaf-dark) 70%, rgba(12,13,12,0) 100%);
  }
  .card--back .leaf-photo {
    background: radial-gradient(circle 210px at 470px 120px, var(--leaf-light) 0%, var(--leaf-mid) 40%, var(--leaf-dark) 70%, rgba(12,13,12,0) 100%);
  }
  .brand {
    position: absolute;
    display: flex;
    align-items: center;
    gap: 10px;
    color: var(--white);
    font-weight: 800;
    letter-spacing: -1px;
    line-height: 1;
  }
  .brand__mark { background: var(--green); }
  .card--front .brand { left: 120px; top: 142px; font-size: 50px; }
  .card--front .brand__mark { width: 34px; height: 34px; }
  .card--back .brand { left: 36px; top: 58px; font-size: 38px; }
  .card--back .brand__mark { width: 26px; height: 26px; }
  .details {
    position: absolute;
    left: 52px;
    top: 120px;
    color: var(--muted);
    font-size: 13px;
    line-height: 1.4;
  }
  .details__role {
    color: var(--green);
    font-weight: 700;
    font-size: 15px;
    letter-spacing: 0.5px;
    text-transform: uppercase;
    margin-bottom: 12px;
  }
  .details__address { margin-bottom: 12px; }
  .contact { list-style: none; }
  .contact li { display: flex; align-items: center; gap: 8px; }
  .contact svg { width: 11px; height: 11px; flex: none; }
  .contact__accent { color: var(--green); }
</style>
</head>
<body>
  <section class="card card--front" aria-label="Card front">
    <div class="leaf-photo" role="img" aria-label="Photograph of green hemp leaves"></div>
    <div class="brand"><span class="brand__mark"></span>alpinleaf</div>
  </section>

  <section class="card card--back" aria-label="Card back">
    <div class="leaf-photo" role="img" aria-label="Photograph of green hemp leaves"></div>
    <div class="brand"><span class="brand__mark"></span>alpinleaf</div>
    <div class="details">
      <p class="details__role">Director</p>
      <p class="details__address">27 Larch Lane,<br>Westbrook, NZ, 4410</p>
      <ul class="contact">
        <li>
          <svg viewBox="0 0 12 12"><path d="M2 1l2 0 1 3-1.3 1a6 6 0 0 0 3.3 3.3L8 7l3 1v2c0 .6-.5 1-1 1A9 9 0 0 1 1 2c0-.5.4-1 1-1z" fill="var(--green)"/></svg>
          +41 (0) 70 555 01 23
        </li>
        <li>
          <svg viewBox="0 0 12 12"><rect x="3" y="0.5" width="6" height="11" rx="1" fill="none" stroke="var(--green)" stroke-width="1.2"/><circle cx="6" cy="9.5" r="0.7" fill="var(--green)"/></svg>
          +44 7700 900 123
        </li>
        <li>
          <svg viewBox="0 0 12 12"><rect x="0.8" y="2.2" width="10.4" height="7.6" fill="none" stroke="var(--green)" stroke-width="1.2"/><path d="M1 2.5l5 4 5-4" fill="none" stroke="var(--green)" stroke-width="1.2"/></svg>
          office@alpinleaf.net
        </li>
        <li>
          <svg viewBox="0 0 12 12"><circle cx="6" cy="6" r="5" fill="none" stroke="var(--green)" stroke-width="1.1"/><ellipse cx="6" cy="6" rx="2.2" ry="5" fill="none" stroke="var(--green)" stroke-width="1"/><path d="M1 6h10" stroke="var(--green)" stroke-width="1"/></svg>
          <span>www.<span class="contact__accent">alpinleaf</span>.net</span>
        </li>
      </ul>
    </div>
  </section>
</body>
</html>
```